Verdana Harvest Co - Business Card Design Project

We need business cards for our business. We grow roots and fruits in Central and South America, we import and distribute in FL, USA. We do fresh and frozen products.

Target Market(s)

Small and big supermarkets, wholesalers, traders, distributors, etc

Industry/Entity Type

Business

```html
<!DOCTYPE html>
<html lang="en">
<head>
<meta charset="utf-8">
<title>Verdana Harvest Co – Business Card</title>
<link rel="stylesheet" href="https://fonts.googleapis.com/css2?family=Questrial&display=swap">
<style>
  :root {
    --stage: #3a3a3a;
    --card: #fbfbfb;
    --card-edge: #e6e6e6;
    --leaf-green: #4f6420;
    --harvest-orange: #e27d12;
    --ink: #2b2b2b;
    --band: #efefef;
    --band-line: #e2e2e2;
  }
  * { margin: 0; padding: 0; box-sizing: border-box; }
  html, body {
    width: 1200px; height: 1116px; overflow: hidden;
    background: var(--stage);
    font-family: "Questrial", "Century Gothic", sans-serif;
  }
  .card {
    position: absolute;
    left: 314px; top: 58px;
    width: 572px; height: 1000px;
    background: linear-gradient(180deg, #ffffff 0%, var(--card) 60%, #f3f3f3 100%);
    border: 1px solid var(--card-edge);
    box-shadow: 0 18px 40px rgba(0,0,0,.45);
  }
  .holder {
    text-align: center;
    margin-top: 70px;
  }
  .holder-name {
    color: var(--leaf-green);
    font-size: 36px;
    font-weight: 400;
    letter-spacing: 1.5px;
  }
  .holder-role {
    color: var(--ink);
    font-size: 21px;
    margin-top: 2px;
  }
  .brand {
    display: flex; align-items: center; justify-content: center;
    gap: 14px;
    margin-top: 86px;
  }
  .brand-dot {
    width: 22px; height: 22px; border-radius: 50%;
    background: var(--leaf-green);
  }
  .brand-name {
    color: var(--harvest-orange);
    font-size: 44px;
    letter-spacing: 1px;
  }
  .contacts {
    list-style: none;
    position: absolute;
    left: 44px; right: 44px; top: 420px;
    padding-top: 62px;
    background: linear-gradient(180deg, var(--band) 0, var(--band) 50px, transparent 50px);
  }
  .contact {
    display: flex; align-items: center; gap: 26px;
    height: 74px;
    margin-bottom: 8px;
    padding-left: 36px;
    background: var(--band);
    color: var(--ink);
    font-size: 26px;
    letter-spacing: .5px;
    white-space: nowrap;
  }
  .contact-icon {
    width: 42px; height: 42px; flex: none;
    display: flex; align-items: center; justify-content: center;
    color: var(--harvest-orange);
  }
  .marker-circle { display: block; width: 38px; height: 38px; border-radius: 50%; background: var(--harvest-orange); }
  .marker-square { display: block; width: 36px; height: 36px; background: var(--harvest-orange); }
</style>
</head>
<body>
  <main class="card">
    <header class="holder">
      <h1 class="holder-name">Marco Ellison</h1>
      <p class="holder-role">Founder</p>
    </header>

    <div class="brand">
      <span class="brand-dot"></span>
      <span class="brand-name">Verdana Harvest Co</span>
    </div>

    <ul class="contacts">
      <li class="contact"><span class="contact-icon"><span class="marker-circle"></span></span>marcoellison</li>
      <li class="contact"><span class="contact-icon"><span class="marker-square"></span></span>@NorthLedger_HQ</li>
      <li class="contact">
        <svg class="contact-icon" viewBox="0 0 24 24" aria-hidden="true">
          <path fill="currentColor" d="M12 2a7 7 0 0 0-7 7c0 5.2 7 13 7 13s7-7.8 7-13a7 7 0 0 0-7-7zm0 9.5A2.5 2.5 0 1 1 12 6.5a2.5 2.5 0 0 1 0 5z"/>
        </svg>Address Details Here</li>
      <li class="contact"><span class="contact-icon"><span class="marker-square"></span></span>nlpage.net/NorthLedgerCo</li>
      <li class="contact">
        <svg class="contact-icon" viewBox="0 0 24 24" aria-hidden="true">
          <rect x="2" y="5" width="20" height="14" fill="currentColor"/>
          <path d="M2 5l10 8 10-8" fill="none" stroke="#fff" stroke-width="1.6"/>
        </svg>mellison@northledger.io</li>
      <li class="contact">
        <svg class="contact-icon" viewBox="0 0 24 24" aria-hidden="true">
          <circle cx="12" cy="12" r="10" fill="currentColor"/>
          <g fill="none" stroke="#fff" stroke-width="1.4">
            <ellipse cx="12" cy="12" rx="4.5" ry="10"/>
            <path d="M2 12h20M4 7h16M4 17h16"/>
          </g>
        </svg>www.northledger.io</li>
    </ul>
  </main>
</body>
</html>
```